Kestrel Home Business Card Design

We need a business card for a Building company based in Queensland, Australia. Our colours are orange black and we do base all our homes design names and other aspect of our business on astrology. We want the consumer to perceive the company as professional and to attract investors to our company.We have over 20 years in the building industry.We pride ourselves on our innovation of designs and making the building process for anyone from families to investor a smooth and simple experience.
Business
Amelia Prichard0411752116PO Box 454, Mudgeerbaameliaprichard@zodiachomes.com

```html
<!DOCTYPE html>
<html lang="en">
<head>
<meta charset="utf-8">
<title>Kestrel Homes Business Card</title>
<link rel="stylesheet" href="https://fonts.googleapis.com/css2?family=Montserrat:wght@600;700&family=Open+Sans:wght@400;700&display=swap">
<style>
  :root {
    --bg: #e4e4e4;
    --black: #0d0d0d;
    --black-soft: #242424;
    --orange: #e77a1a;
    --white: #ffffff;
    --ink: #1a1a1a;
  }
  * { box-sizing: border-box; margin: 0; padding: 0; }
  html, body { width: 1200px; height: 852px; overflow: hidden; }
  body {
    background: var(--bg);
    font-family: "Open Sans", sans-serif;
    position: relative;
  }
  .card {
    position: absolute;
    top: 281px;
    width: 500px;
    height: 290px;
    border-radius: 24px;
    overflow: hidden;
    box-shadow: 0 8px 18px rgba(0,0,0,0.25);
  }
  .card-front {
    left: 70px;
    background: linear-gradient(135deg, var(--black-soft) 0%, var(--black) 60%);
    display: flex;
    flex-direction: column;
    align-items: center;
    justify-content: center;
    gap: 18px;
  }
  .brand-dot {
    width: 70px;
    height: 70px;
    border-radius: 50%;
    background: var(--orange);
  }
  .brand-name {
    font-family: "Montserrat", sans-serif;
    font-weight: 700;
    font-size: 38px;
    letter-spacing: -0.5px;
    color: var(--white);
    white-space: nowrap;
  }
  .card-back {
    left: 630px;
    background: var(--orange);
  }
  .back-brand {
    position: absolute;
    top: 28px;
    right: 34px;
    display: flex;
    flex-direction: column;
    align-items: center;
    gap: 14px;
  }
  .back-brand .brand-dot {
    width: 82px;
    height: 82px;
    background: var(--black);
  }
  .back-brand .brand-name {
    color: var(--ink);
    font-size: 32px;
  }
  .holder {
    position: absolute;
    left: 30px;
    top: 120px;
    color: var(--ink);
  }
  .holder-name {
    font-family: "Montserrat", sans-serif;
    font-weight: 700;
    font-size: 17px;
  }
  .holder-role {
    font-size: 11px;
    margin-top: 3px;
  }
  .contacts {
    position: absolute;
    left: 30px;
    bottom: 26px;
    list-style: none;
    color: var(--ink);
    font-size: 12px;
    line-height: 1.55;
  }
  .contacts li { display: flex; align-items: center; gap: 10px; white-space: nowrap; }
  .contacts svg { width: 12px; height: 12px; fill: var(--white); flex: none; }
  .swoosh {
    position: absolute;
    right: 0;
    bottom: 0;
    width: 500px;
    height: 290px;
  }
</style>
</head>
<body>
  <section class="card card-front">
    <div class="brand-dot"></div>
    <div class="brand-name">Kestrel Homes</div>
  </section>

  <section class="card card-back">
    <svg class="swoosh" viewBox="0 0 500 290" preserveAspectRatio="none" aria-hidden="true">
      <path d="M500 178 C430 200 360 250 250 290 L500 290 Z" fill="#0d0d0d"/>
      <path d="M500 196 C440 220 380 262 300 290 L500 290 Z" fill="#ffffff"/>
    </svg>

    <div class="back-brand">
      <div class="brand-dot"></div>
      <div class="brand-name">Kestrel Homes</div>
    </div>

    <div class="holder">
      <div class="holder-name">Harriet Colvane</div>
      <div class="holder-role">Owner / Proprietor</div>
    </div>

    <ul class="contacts">
      <li>
        <svg viewBox="0 0 12 12"><rect x="3" y="0.5" width="6" height="11" rx="1.2"/></svg>
        0487309625
      </li>
      <li>
        <svg viewBox="0 0 12 12"><path d="M6 0.5a4 4 0 0 1 4 4c0 3-4 7-4 7s-4-4-4-7a4 4 0 0 1 4-4z"/></svg>
        PO Box 872, Wattleby
      </li>
      <li>
        <svg viewBox="0 0 12 12"><rect x="0.5" y="2.5" width="11" height="7" rx="0.8"/></svg>
        harrietcolvane@kestrelhomes.example
      </li>
    </ul>
  </section>
</body>
</html>
```